Unique Business Card Design

Unique Business Card design for our orthotic and prosthetic company. Our logo is on our website, color is light blue. Unique shape (artificial leg shaped, vertical, etc..) preferred. Logo, business name, individual name and basic demographics needed.

Industry/Entity Type

Business

Contact Information for Business Card

Logo, Industry, Phone # Logo, "Prosthetic & Orthotic Services" Place to add individual name and contact info

Colors
cee9f5

Requirements
Must have
• The icon must be there, placement of "Prosthetic & Orthotic Services" can be moved
Nice to have
• Like the mix of light blue, and a little darker blue. One design included the icons from my website which was a nice touch

```html
<!DOCTYPE html>
<html lang="en">
<head>
<meta charset="utf-8">
<title>Limbwright Inc. — Business Card</title>
<link rel="stylesheet" href="https://fonts.googleapis.com/css2?family=Open+Sans:wght@600&family=PT+Serif:ital@0;1&display=swap">
<style>
  :root {
    --backdrop: #231f20;
    --card: #bcdff3;
    --brand-blue: #0a5fb4;
    --ink: #222222;
    --limb: #ffffff;
  }
  * { margin: 0; padding: 0; box-sizing: border-box; }
  html, body { width: 1200px; height: 853px; overflow: hidden; background: var(--backdrop); }
  .canvas { position: relative; width: 1200px; height: 853px; }

  .card {
    position: absolute; left: 210px; top: 186px; width: 780px; height: 480px;
    background: var(--card);
    border-radius: 0 112px 0 136px;
    font-family: "PT Serif", Georgia, serif;
    color: var(--ink);
  }

  .limb-illustration {
    position: absolute; left: 100px; top: 62px; width: 112px; height: 356px;
    background: linear-gradient(180deg, #ffffff 0%, #f4f9fd 100%);
    border-radius: 14px 14px 10px 30px;
  }

  .brand-mark {
    position: absolute; left: 276px; top: 53px; width: 112px; height: 112px;
    border-radius: 50%; background: var(--brand-blue);
  }
  .brand-name {
    position: absolute; left: 404px; top: 74px;
    font-family: "Open Sans", Arial, sans-serif; font-weight: 600;
    font-size: 35px; line-height: 40px; letter-spacing: -0.5px;
    color: var(--brand-blue); white-space: nowrap;
  }
  .brand-rule {
    position: absolute; left: 410px; top: 112px; width: 279px; height: 4px;
    background: var(--brand-blue);
  }
  .brand-tagline {
    position: absolute; left: 416px; top: 119px;
    font-style: italic; font-size: 20px; line-height: 26px;
    color: var(--brand-blue); white-space: nowrap;
  }

  .person-name {
    position: absolute; left: 410px; top: 200px;
    font-size: 29px; line-height: 32px; white-space: nowrap;
  }
  .person-title {
    position: absolute; left: 410px; top: 230px;
    font-size: 20px; line-height: 24px; color: var(--brand-blue); white-space: nowrap;
  }

  .contact-list { list-style: none; }
  .contact-item {
    position: absolute; left: 416px; height: 24px;
    display: flex; align-items: center;
    font-size: 21px; line-height: 24px; white-space: nowrap;
  }
  .contact-icon { width: 14px; height: 14px; margin-right: 10px; fill: var(--brand-blue); flex: none; }
  .contact-item.phone-mobile { top: 278px; }
  .contact-item.phone-office { top: 305px; }
  .contact-item.email { top: 328px; }
  .contact-item.web { top: 352px; }
  .contact-item.address { top: 384px; align-items: flex-start; height: auto; }
  .contact-item.address .contact-icon { margin-top: 4px; }
  .address-lines { line-height: 25px; }
</style>
</head>
<body>
<div class="canvas">
  <section class="card">
    <div class="limb-illustration" role="img" aria-label="Silhouette of a prosthetic lower leg with socket, pylon and foot"></div>

    <div class="brand-mark" aria-hidden="true"></div>
    <div class="brand-name">LIMBWRIGHT INC.</div>
    <div class="brand-rule"></div>
    <div class="brand-tagline">Prosthetic &amp; Orthotic Services</div>

    <h1 class="person-name" style="font-weight:400">Marla Teversen</h1>
    <p class="person-title">Orthotist / Prosthetist</p>

    <ul class="contact-list">
      <li class="contact-item phone-mobile">
        <svg class="contact-icon" viewBox="0 0 14 14"><path d="M4 0h6a1.5 1.5 0 0 1 1.5 1.5v11A1.5 1.5 0 0 1 10 14H4a1.5 1.5 0 0 1-1.5-1.5v-11A1.5 1.5 0 0 1 4 0zm0 2v9h6V2zm3 9.8a.9.9 0 1 0 0 1.8.9.9 0 0 0 0-1.8z"/></svg>
        845-555-0182
      </li>
      <li class="contact-item phone-office">
        <svg class="contact-icon" viewBox="0 0 14 14"><path d="M3 .5l2.2 2.8-1.3 1.6c.9 2 2.6 3.6 4.6 4.5l1.6-1.3L13 10.3 11.7 13C6 13 1 8 1 2.3z"/></svg>
        718-555-0146
      </li>
      <li class="contact-item email">
        <svg class="contact-icon" viewBox="0 0 14 14"><path d="M0 3h14v1.2L7 8.3 0 4.2zm0 2.6l7 4 7-4V12H0z"/></svg>
        limbwright@mailbay.net
      </li>
      <li class="contact-item web">
        <svg class="contact-icon" viewBox="0 0 14 14"><path d="M7 0a7 7 0 1 0 0 14A7 7 0 0 0 7 0zm-.7 1.6v3H4.2c.4-1.5 1.2-2.7 2.1-3zm1.4 0c.9.3 1.7 1.5 2.1 3H7.7zM1.6 6.3h2.3a13 13 0 0 0 0 1.4H1.6a5.5 5.5 0 0 1 0-1.4zm3.7 0h1v1.4h-1a10 10 0 0 1 0-1.4zm2.4 0h1a10 10 0 0 1 0 1.4h-1zm2.4 0h2.3a5.5 5.5 0 0 1 0 1.4h-2.3a13 13 0 0 0 0-1.4zM4.2 9.4h2.1v3c-.9-.3-1.7-1.5-2.1-3zm3.5 0h2.1c-.4 1.5-1.2 2.7-2.1 3z"/></svg>
        www.limbwright-demo.com
      </li>
      <li class="contact-item address">
        <svg class="contact-icon" viewBox="0 0 14 14"><path d="M7 0a4.5 4.5 0 0 0-4.5 4.5C2.5 8 7 14 7 14s4.5-6 4.5-9.5A4.5 4.5 0 0 0 7 0zm0 2.6a1.9 1.9 0 1 1 0 3.8 1.9 1.9 0 0 1 0-3.8z"/></svg>
        <span class="address-lines">2390 West 14th Avenue<br>Fairbridge, NY 10099</span>
      </li>
    </ul>
  </section>
</div>
</body>
</html>
```